Alloy wheel repair business needs a website

Install logo previously purchased from makerhive, toolbar with dropdowns. services, gallery, clients , contact ect
Maybe mission statment

Target Market(s)

vehicle owners, auto dealers,insurance companies,

Industry/Entity Type

Alloy Wheel Repair

Coding

Coded - Design and coding required

Number of Pages Required

4 page

Font styles to use
Sans Serif

Colors
0054AA
0677BA
7BADD7
CADEEF
E8F1F8

```html
<!DOCTYPE html>
<html lang="en">
<head>
<meta charset="utf-8">
<title>Rimforge Wheels – Alloy Wheel Repair</title>
<link rel="stylesheet" href="https://fonts.googleapis.com/css2?family=Montserrat:wght@400;500;600;700&display=swap">
<style>
:root{
  --blue-deep:#0054AA;
  --blue:#0677BA;
  --blue-mid:#3d86c8;
  --blue-soft:#7BADD7;
  --blue-pale:#CADEEF;
  --blue-mist:#E8F1F8;
  --ink:#111111;
  --dark:#16181d;
  --dark-2:#22252b;
  --white:#ffffff;
  --light:#eef0f2;
}
*{box-sizing:border-box;margin:0;padding:0}
html,body{width:1200px;height:3576px;overflow:hidden}
body{font-family:"Montserrat",sans-serif;color:var(--ink);background:var(--white);position:relative}
.abs{position:absolute}

/* header */
.site-header{position:absolute;left:0;top:0;width:1200px;height:93px;background:var(--white);border-bottom:1px solid #ddd}
.brand{position:absolute;left:125px;top:24px;display:flex;align-items:center;gap:10px}
.brand-dot{width:34px;height:34px;border-radius:50%;background:var(--blue)}
.brand-name{font-weight:700;font-size:26px;color:var(--blue);letter-spacing:1px}
.top-contact{position:absolute;right:112px;top:19px;font-size:14px;color:#222}
.main-nav{position:absolute;right:112px;top:49px;display:flex;gap:29px;font-weight:600;font-size:17.5px}
.main-nav a{color:var(--ink);text-decoration:none}

/* hero */
.hero{position:absolute;left:0;top:93px;width:1200px;height:640px}
.hero-photo{position:absolute;left:0;top:0;width:1200px;height:640px}
.hero-title{left:697px;top:240px;font-size:44px;font-weight:700;color:var(--white);line-height:61px}
.hero-text{left:697px;top:378px;width:392px;font-size:16px;line-height:24px;color:var(--white);text-align:justify}
.btn{display:inline-flex;align-items:center;justify-content:center;font-family:inherit;font-weight:700;font-size:17px;border-radius:9px;height:40px;padding:0 11px;text-decoration:none}
.btn-light{background:var(--white);color:var(--ink)}
.btn-dark{background:var(--ink);color:var(--white)}

/* section titles */
.section-title{position:absolute;left:0;width:1200px;text-align:center;font-weight:700;font-size:36px;color:var(--blue-mid)}

/* services */
.service{position:absolute;top:865px;width:214px;text-align:center}
.service-photo{width:214px;height:184px;border-radius:14px}
.service-name{margin-top:11px;font-weight:700;font-size:17px;color:var(--blue-mid)}
.service-text{margin-top:4px;font-size:16px;line-height:24px;color:#222;width:220px;margin-left:-3px}

/* about */
.about{position:absolute;left:0;top:1314px;width:1200px;height:544px;background:linear-gradient(90deg,#1a1c22,#2b2e35 70%,#1d1f25)}
.about-ring{position:absolute;left:182px;top:1401px;width:345px;height:345px;border:2px solid var(--blue-mid);border-radius:50%}
.about-photo{position:absolute;left:208px;top:1417px;width:324px;height:314px;border-radius:50%;background:radial-gradient(circle at 55% 50%,#d8d8da 0%,#7d7f85 30%,#2e3036 65%,#151619 100%)}
.about-title{left:600px;top:1390px;font-size:36px;font-weight:700;color:var(--white)}
.about-text{left:600px;top:1462px;width:489px;font-size:17px;line-height:24px;color:var(--white);text-align:justify}

/* gallery */
.gallery{position:absolute;left:0;top:1858px;width:1200px;height:760px;background:radial-gradient(circle at 80% 30%,#ffffff,#e6e9ec 70%)}
.gallery-photo{position:absolute;border-radius:11px}

/* mission */
.mission{position:absolute;left:0;top:2618px;width:1200px;height:377px;background:linear-gradient(180deg,#1b1d22,#25282e)}
.mission-title{left:0;width:1200px;text-align:center;top:2692px;font-size:36px;font-weight:700;color:var(--white)}
.mission-text{left:150px;width:900px;top:2770px;text-align:center;font-size:17px;line-height:24px;color:var(--white)}

/* contact */
.contact{position:absolute;left:0;top:2995px;width:1200px;height:526px;background:linear-gradient(135deg,#f6f6f7,#ececee)}
.contact-title{left:111px;top:3076px;font-size:36px;font-weight:700}
.field{position:absolute;border:1.5px solid #555;border-radius:10px;background:transparent;font-size:17px;color:#444;padding:6px 14px;font-family:inherit}
.submit{position:absolute;left:328px;top:3397px;width:126px;height:38px;background:#000;color:var(--white);font-weight:700;font-size:18px;display:flex;align-items:center;justify-content:center}
.contact-photo{position:absolute;left:751px;top:3109px;width:296px;height:312px;border-radius:10px;background:linear-gradient(135deg,#4a4c52,#1c1d21 55%,#2e3035);box-shadow:0 8px 18px rgba(0,0,0,.3)}
.contact-frame{position:absolute;left:726px;top:3084px;width:295px;height:312px;border:2px solid var(--blue-mid);border-radius:10px}

/* footer */
.site-footer{position:absolute;left:0;top:3521px;width:1200px;height:55px;background:#000;color:var(--white);font-size:16px;display:flex;align-items:center;justify-content:center}
</style>
</head>
<body>

<header class="site-header">
  <div class="brand"><span class="brand-dot"></span><span class="brand-name">RIMFORGE</span></div>
  <div class="top-contact">Mail: hello@rimforgewheels.example &nbsp;|&nbsp; Phone: +1 555 0142 7788</div>
  <nav class="main-nav">
    <a href="#">Home</a><a href="#">About</a><a href="#">Services</a><a href="#">Gallery</a><a href="#">Clients</a><a href="#">Contact</a>
  </nav>
</header>

<section class="hero">
  <svg class="hero-photo" width="1200" height="640" viewBox="0 0 1200 640">
    <defs>
      <radialGradient id="heroGlow" cx="0.33" cy="0.45" r="0.6">
        <stop offset="0" stop-color="#6a6c72"/>
        <stop offset="0.45" stop-color="#26282d"/>
        <stop offset="1" stop-color="#060607"/>
      </radialGradient>
    </defs>
    <path d="M0 0H1200V490L826 618L0 497Z" fill="url(#heroGlow)" role="img" aria-label="Photo of a dark alloy wheel with tyre"/>
    <path d="M0 497L826 618L1200 490V505L826 620L0 515Z" fill="var(--blue-mid)"/>
    <path d="M0 497L826 618L1200 490" fill="none" stroke="var(--blue-mid)" stroke-width="14"/>
  </svg>
</section>
<h1 class="abs hero-title">Welcome To<br>Rimforge Wheels</h1>
<p class="abs hero-text">Lorem ipsum dolor sit amet, consectetur adipiscing elit, sed do eiusmod tempor incididunt ut labore et dolore magna aliqua.</p>
<a class="abs btn btn-light" href="#" style="left:697px;top:475px">Learn More</a>

<h2 class="section-title" style="top:792px">Our Services</h2>
<div class="service" style="left:126px"><div class="service-photo" role="img" aria-label="Technician fitting a tyre on an alloy wheel" style="background:linear-gradient(135deg,#3a3c42,#111214)"></div><div class="service-name">Service 1</div><p class="service-text">Lorem ipsum dolor sit amet, consectetur adipiscing elit, sed do eius-</p></div>
<div class="service" style="left:371px"><div class="service-photo" role="img" aria-label="Close-up of silver alloy wheel spokes" style="background:linear-gradient(135deg,#bfc1c4,#2a2b2f)"></div><div class="service-name">Service 1</div><p class="service-text">Lorem ipsum dolor sit amet, consectetur adipiscing elit, sed do eius-</p></div>
<div class="service" style="left:615px"><div class="service-photo" role="img" aria-label="Hands repairing an alloy rim" style="background:linear-gradient(135deg,#9a9ca0,#4a4c50)"></div><div class="service-name">Service 1</div><p class="service-text">Lorem ipsum dolor sit amet, consectetur adipiscing elit, sed do eius-</p></div>
<div class="service" style="left:860px"><div class="service-photo" role="img" aria-label="Bronze alloy wheel in a workshop" style="background:linear-gradient(135deg,#5a4a3c,#1a1817)"></div><div class="service-name">Service 1</div><p class="service-text">Lorem ipsum dolor sit amet, consectetur adipiscing elit, sed do eius-</p></div>
<a class="abs btn btn-dark" href="#" style="left:540px;top:1189px">View More</a>

<section class="about"></section>
<div class="about-photo" role="img" aria-label="Black and silver alloy wheel"></div>
<div class="about-ring"></div>
<h2 class="abs about-title">About Us</h2>
<div class="abs about-text">
  <p>Lorem ipsum dolor sit amet, consectetur adipiscing elit, sed do eiusmod tempor incididunt ut labore et dolore magna aliqua. Quis ipsum suspendisse ultrices gravida. Risus commodo viverra maecenas accumsan lacus vel facilisis.</p>
  <p style="margin-top:24px">Sed ut perspiciatis unde omnis iste natus error sit voluptatem accusantium doloremque laudantium, totam rem aperiam, eaque ipsa quae ab illo inventore veritatis et quasi architecto beatae vitae dicta sunt explicabo.</p>
</div>
<a class="abs btn btn-light" href="#" style="left:600px;top:1733px">Learn More</a>

<section class="gallery"></section>
<h2 class="section-title" style="top:1934px">Gallery</h2>
<div class="gallery-photo" role="img" aria-label="Alloy wheel with orange accents" style="left:111px;top:2004px;width:418px;height:213px;background:linear-gradient(90deg,#1c1d20,#6a4a3a 70%,#2a2020)"></div>
<div class="gallery-photo" role="img" aria-label="Alloy wheel with red brake caliper" style="left:554px;top:2004px;width:254px;height:213px;background:linear-gradient(135deg,#7a2a1e,#2a2a2d 60%)"></div>
<div class="gallery-photo" role="img" aria-label="Carbon alloy wheel with red hub" style="left:833px;top:2004px;width:255px;height:213px;background:linear-gradient(135deg,#3a4a42,#1a1c1e 60%,#6a6c70)"></div>
<div class="gallery-photo" role="img" aria-label="Mechanic holding a chrome wheel" style="left:111px;top:2238px;width:254px;height:212px;background:linear-gradient(135deg,#2a3a6a,#c9c9cb 55%,#3a3a3c)"></div>
<div class="gallery-photo" role="img" aria-label="Workshop staff handing over a wheel" style="left:390px;top:2238px;width:256px;height:212px;background:linear-gradient(135deg,#c8c3b8,#5a5c60 60%,#2a2a2c)"></div>
<div class="gallery-photo" role="img" aria-label="Car wheel at sunset" style="left:671px;top:2238px;width:417px;height:212px;background:linear-gradient(90deg,#c98a2a,#5a4a30 45%,#2a2a2c)"></div>
<a class="abs btn btn-dark" href="#" style="left:539px;top:2493px">View More</a>

<section class="mission"></section>
<h2 class="abs mission-title">Mission</h2>
<p class="abs mission-text">Lorem ipsum dolor sit amet, consectetur adipiscing elit, sed do eiusmod tempor incididunt ut labore et dolore magna aliqua. Quis ipsum suspendisse ultrices gravida. Risus commodo viverra maecenas accumsan lacus vel facilisis.</p>
<a class="abs btn btn-light" href="#" style="left:539px;top:2870px">Learn More</a>

<section class="contact"></section>
<h2 class="abs contact-title">Contact Us</h2>
<div class="field" style="left:112px;top:3134px;width:253px;height:34px">First name</div>
<div class="field" style="left:415px;top:3134px;width:253px;height:34px">Last name</div>
<div class="field" style="left:112px;top:3196px;width:253px;height:35px">Email</div>
<div class="field" style="left:415px;top:3196px;width:253px;height:35px">Phone Number</div>
<div class="field" style="left:112px;top:3258px;width:556px;height:112px">Message</div>
<div class="submit">Submit</div>
<div class="contact-photo" role="img" aria-label="Stacked tyres with an alloy wheel"></div>
<div class="contact-frame"></div>

<footer class="site-footer">Copyrights 2023 Rimforge Wheels. All Rights Reserved.</footer>

</body>
</html>
```